Business Card Design

My business is writing crime novels to entertain readers. I write legal thrillers and mysteries. I need a card for publishers, agents, other authors, and media.

Industry/Entity Type

Legal

Contact Information for Business Card

Paul Derrow
www.derrowfiction.example
pauljderrow@inkpost.example
0064 27 5190472

```html
<!DOCTYPE html>
<html lang="en">
<head>
<meta charset="utf-8">
<title>Paul Derrow – Business Card</title>
<link rel="stylesheet" href="https://fonts.googleapis.com/css2?family=Lato:wght@400&family=Open+Sans:wght@400&display=swap">
<style>
  :root {
    --page-bg: #e9e9ea;
    --card-light: #fbfbf3;
    --card-yellow: #f3f2b6;
    --card-olive: #dcdcae;
    --ink-green: #127a3e;
    --portrait-dark: #2e2e2c;
    --portrait-mid: #8a7a6e;
    --portrait-light: #e7e3d6;
  }
  * { margin: 0; padding: 0; box-sizing: border-box; }
  html, body {
    width: 1200px;
    height: 864px;
    overflow: hidden;
    background: var(--page-bg);
  }
  .stage {
    width: 1200px;
    height: 864px;
    display: flex;
    align-items: center;
    justify-content: center;
  }
  .business-card {
    position: relative;
    width: 1050px;
    height: 600px;
    overflow: hidden;
    background:
      radial-gradient(ellipse 70% 75% at 62% 18%, var(--card-yellow) 0%, rgba(243,242,182,0) 70%),
      linear-gradient(160deg, var(--card-olive) 0%, #ecebc6 35%, var(--card-light) 75%);
    box-shadow: 0 10px 30px rgba(0,0,0,0.18);
  }
  .identity {
    position: absolute;
    left: 92px;
    top: 150px;
    color: var(--ink-green);
    font-family: "Lato", sans-serif;
  }
  .identity__name {
    font-size: 50px;
    font-weight: 400;
    letter-spacing: 0.5px;
    line-height: 1;
    text-transform: uppercase;
  }
  .identity__role {
    margin-top: 8px;
    margin-left: 8px;
    font-size: 19px;
    text-transform: uppercase;
  }
  .contact-list {
    position: absolute;
    left: 92px;
    top: 388px;
    list-style: none;
    font-family: "Open Sans", sans-serif;
    color: var(--ink-green);
    font-size: 22px;
    letter-spacing: 1.4px;
  }
  .contact-list__item {
    display: flex;
    align-items: center;
    height: 50px;
  }
  .contact-list__icon {
    width: 24px;
    height: 24px;
    margin-right: 18px;
    flex: none;
  }
  .portrait {
    position: absolute;
    right: 22px;
    bottom: 0;
    width: 370px;
    height: 488px;
    border-radius: 150px 150px 0 0;
    background: linear-gradient(180deg,
      var(--portrait-mid) 0%,
      var(--portrait-light) 40%,
      var(--portrait-dark) 62%,
      var(--portrait-dark) 100%);
    opacity: 0.85;
  }
</style>
</head>
<body>
  <main class="stage">
    <article class="business-card">
      <header class="identity">
        <h1 class="identity__name">Paul Derrow</h1>
        <p class="identity__role">Owner</p>
      </header>

      <ul class="contact-list">
        <li class="contact-list__item">
          <svg class="contact-list__icon" viewBox="0 0 24 24" aria-hidden="true">
            <rect x="2" y="3" width="20" height="14" fill="none" stroke="currentColor" stroke-width="2.4"/>
            <rect x="7" y="19" width="10" height="2.4" fill="currentColor"/>
          </svg>
          <span>www.derrowfiction.example</span>
        </li>
        <li class="contact-list__item">
          <svg class="contact-list__icon" viewBox="0 0 24 24" aria-hidden="true">
            <rect x="1" y="5" width="22" height="15" fill="currentColor"/>
            <path d="M2 6 L12 14 L22 6 M2 19 L9 12 M22 19 L15 12" fill="none" stroke="#fbfbf3" stroke-width="1.5"/>
          </svg>
          <span>pauljderrow@inkpost.example</span>
        </li>
        <li class="contact-list__item">
          <svg class="contact-list__icon" viewBox="0 0 24 24" aria-hidden="true">
            <path d="M2 9 C2 4 22 4 22 9 L22 11 L17 11 L17 8 L7 8 L7 11 L2 11 Z" fill="currentColor"/>
            <path d="M6 12 L18 12 L21 21 L3 21 Z" fill="currentColor"/>
            <circle cx="12" cy="16.5" r="2.4" fill="#fbfbf3"/>
          </svg>
          <span>0064 27 5190472</span>
        </li>
      </ul>

      <div class="portrait" role="img" aria-label="Head-and-shoulders portrait of the author in a dark jacket and white shirt"></div>
    </article>
  </main>
</body>
</html>
```